Fin-Tech Firm Captivating Business Card Design

We need a logo design as well to compliment this business card.

We are a new startup based in Singapore called 'Brevora Technologies'.

We develop an array of financial solutions ranging from payment convenience to forex trading and remittance.

Our initial product is Pim - an application which allows user to pre-order food items which would be ready for pickup upon arrival.

We would like to see designs being in black and silver or whatever that looks appealing and exudes a fun and professional feel.

We're not picky as long as it doesn't look like common business cards will do.

I do have a current logo which i do not really like. It will be attached for reference sake

Info:

Brevora Technologies Pte. Ltd.
Company Registration no. 201678213K

FILE TO BE IN .AI and .PSD

Target Market(s)

-F&B (Online-Ordering)
-Finance(P2P Lending and Forex)

Industry/Entity Type

Finance

Contact Information for Business Card

Name
Position
Contact
Email
Address: 47 Merrow Street, Calder House, #14-03 Singapore 068215

Adrian Teo
Founder, Managing Director
+65 98471360
adrian.t@brevoratech.com

Kai Loh
Founder, Executive Director
+65 96603847
kai.l@brevoratech.com

Logo Text

Brevora Technologies

Font styles to use
Sans Serif

Requirements
Must have
• Something that has word play about link brev
• Minimalistic but also something that catches The Eye
• Gold/silver on white/black might be nice
• Animal logo ; horse, eagle, bull or bear
Nice to have
• Just make it look fun and cute
• Just a suggestion to make the Y of brevora stand out
Should not have
• Any landmarks of singapore
• Exclude Pte. Ltd.

```html
<!DOCTYPE html>
<html lang="en">
<head>
<meta charset="utf-8">
<title>Brevora Technologies – Business Card</title>
<link href="https://fonts.googleapis.com/css2?family=Open+Sans:wght@400;600;700&display=swap" rel="stylesheet">
<style>
  :root {
    --amber: #f3a712;
    --charcoal: #2b2b2d;
    --paper: #ffffff;
    --backdrop: #ecebe8;
  }
  * { margin: 0; padding: 0; box-sizing: border-box; }
  html, body { width: 1200px; height: 900px; overflow: hidden; }
  body {
    background: var(--backdrop);
    font-family: "Open Sans", Arial, sans-serif;
    position: relative;
  }
  .card {
    position: absolute;
    box-shadow: 0 6px 18px rgba(0,0,0,0.18);
    overflow: hidden;
  }
  .card-front {
    left: 78px; top: 35px; width: 587px; height: 362px;
    background: var(--paper);
  }
  .card-back {
    left: 388px; top: 505px; width: 567px; height: 352px;
    background: var(--amber);
  }
  .front-bands { position: absolute; left: 0; top: 0; }
  .brand { position: absolute; display: flex; align-items: center; }
  .brand-mark {
    border-radius: 50%;
    flex: none;
  }
  .brand-name {
    font-weight: 400;
    line-height: 1;
  }
  .brand-name .word { display: block; font-size: 52px; letter-spacing: 1px; }
  .brand-name .legal { display: block; font-size: 21px; margin-top: 6px; }
  .card-front .brand { left: 104px; top: 36px; }
  .card-front .brand-mark { width: 112px; height: 112px; border: 5px solid var(--charcoal); margin-right: 22px; }
  .card-front .brand-name { color: var(--amber); }
  .card-back .brand { left: 87px; top: 120px; }
  .card-back .brand-mark { width: 100px; height: 100px; border: 4px solid var(--paper); margin-right: 22px; }
  .card-back .brand-name { color: var(--paper); }

  .contact {
    position: absolute; left: 0; top: 226px; width: 312px;
    color: var(--paper); font-size: 14.5px; text-align: right;
  }
  .contact-line { display: flex; justify-content: flex-end; align-items: center; gap: 6px; height: 25px; }
  .contact-line svg { flex: none; }
  .registration { font-weight: 700; font-size: 14.5px; margin-top: 8px; text-align: left; padding-left: 17px; white-space: nowrap; }
  .person {
    position: absolute; left: 338px; top: 211px; color: var(--paper);
  }
  .person-name { font-weight: 700; font-size: 19px; line-height: 26px; }
  .person-role { font-size: 15px; line-height: 24px; }
  .person-address { font-size: 15px; line-height: 25px; margin-top: 7px; }
</style>
</head>
<body>
  <section class="card card-front" aria-label="Business card, front">
    <svg class="front-bands" width="587" height="362" viewBox="0 0 587 362">
      <polygon points="0,172 404,172 388,197 0,197" fill="var(--charcoal)"/>
      <polygon points="414,164 587,164 587,362 0,362 0,201 391,201" fill="var(--amber)"/>
    </svg>
    <div class="brand">
      <span class="brand-mark"></span>
      <span class="brand-name"><span class="word">BREVORA</span><span class="legal">Technologies Pte. Ltd</span></span>
    </div>
    <div class="contact">
      <div class="contact-line">+65 98471360
        <svg width="11" height="11" viewBox="0 0 24 24"><path fill="#fff" d="M6.6 10.8a15 15 0 0 0 6.6 6.6l2.2-2.2c.3-.3.7-.4 1-.2 1.1.4 2.3.6 3.6.6.6 0 1 .4 1 1V20c0 .6-.4 1-1 1A17 17 0 0 1 3 4c0-.6.4-1 1-1h3.5c.6 0 1 .4 1 1 0 1.3.2 2.5.6 3.6.1.3 0 .7-.2 1z"/></svg>
      </div>
      <div class="contact-line">adrian.t@brevoratech.com
        <svg width="12" height="9" viewBox="0 0 24 18"><rect width="24" height="18" rx="2" fill="#fff"/><path d="M1 1l11 9 11-9" fill="none" stroke="#f3a712" stroke-width="2"/></svg>
      </div>
      <div class="registration">Company Registration no. 201678213K</div>
    </div>
    <div class="person">
      <div class="person-name">Adrian Teo</div>
      <div class="person-role">Founder, Managing Director</div>
      <div class="person-address">47 Merrow Street, Calder House,<br>#14-03 Singapore 068215</div>
    </div>
  </section>

  <section class="card card-back" aria-label="Business card, back">
    <div class="brand">
      <span class="brand-mark"></span>
      <span class="brand-name"><span class="word">BREVORA</span><span class="legal">Technologies Pte. Ltd</span></span>
    </div>
  </section>
</body>
</html>
```